Create a memorable Web Design for real estate branding

we are a Minnepolis brokerage and boutique housing specialist with over 27 years of experience in the Global furnished housing industry, servicing the Greater Los Angeles area. Specializing in “warm environments” we offer a customized approach to satisfying our guests and client’s needs by offering a wide array of options in highly desirable areas. Additionally, Lantern Dwelling Partners offers assistance and expertise to home buyers, sellers and investors.

Industry/Entity Type

Real Estate

Number of Pages Required

1 page

Font styles to use
Serif
Sans Serif
Decorative

```html
<!DOCTYPE html>
<html lang="en">
<head>
<meta charset="utf-8">
<title>Lantern Dwelling Partners</title>
<link rel="stylesheet" href="https://fonts.googleapis.com/css2?family=Open+Sans:wght@400;600&family=Roboto+Condensed:wght@400;700&display=swap">
<style>
:root{
  --teal:#14b19b;
  --teal-dark:#0f9985;
  --green:#6cb52d;
  --ink:#333;
  --muted:#666;
  --line:#d9d9d9;
  --panel:#f4f4f4;
  --footer:#1e5a49;
  --footer-line:#2f6f5c;
  --footer-text:#a9cfc2;
  --bottom:#113c30;
}
*{margin:0;padding:0;box-sizing:border-box}
html,body{width:726px;height:1200px;overflow:hidden;background:#fff}
body{position:relative;font-family:'Open Sans',sans-serif;color:var(--ink)}
.abs{position:absolute}
.cond{font-family:'Roboto Condensed',sans-serif}

/* header */
.brand{left:85px;top:18px;color:var(--teal);font-weight:600;line-height:1}
.brand .name{font-size:19px}
.brand .sub{font-size:11px;letter-spacing:1px;margin-top:3px;text-align:right;width:130px}
.contact{top:10px;font-size:8px;color:#555;display:flex;align-items:center;gap:4px}
.contact svg{width:9px;height:9px}
.nav{left:294px;top:30px;display:flex;height:29px;font-size:7.5px;color:#333}
.nav a{display:flex;align-items:center;padding:0 7px;text-decoration:none;color:inherit}
.nav a.active{background:var(--teal);color:#fff;width:48px;justify-content:center;margin-right:2px}

/* hero */
.hero{left:0;top:59px;width:726px;height:347px;background:linear-gradient(180deg,#6f9fb8 0%,#a8c6d3 35%,#4d8a6a 72%,#2c6b4a 100%)}
.hero-title{left:86px;top:283px;font-size:15.5px;color:#fff;font-weight:400}
.hero-text{left:86px;top:307px;font-size:7px;color:#fff;line-height:1.4;width:180px}
.dots{left:84px;top:350px;display:flex;gap:3px}
.dots i{width:7px;height:7px;border-radius:50%;background:#ddd}
.dots i:first-child{background:var(--teal)}

/* news */
.news{left:0;top:406px;width:726px;height:38px;border-bottom:1px solid var(--line)}
.news-title{left:85px;top:11px;font-size:11.5px;color:var(--teal);font-weight:600}
.news-sep{left:177px;top:8px;height:22px;border-left:1px dashed #ccc}
.news-text{left:186px;top:14px;font-size:7.8px;color:#666}

.h2{font-size:11.5px;color:var(--green)}
.rule{height:1px;background:var(--line)}
.copy{font-size:7.6px;color:var(--muted);line-height:1.55}

/* projects */
.card{width:177px;height:145px;background:var(--panel);border:1px solid #e2e2e2}
.card .title{position:absolute;left:9px;top:8px;font-size:8.5px;color:var(--teal)}
.card .title span{color:#444}
.card .photo{position:absolute;left:10px;top:22px;width:155px;height:61px;border:2px solid #fff;outline:1px solid #ddd}
.card .info{position:absolute;left:10px;top:91px;font-size:7.8px;color:#555;line-height:1.55}
.btn{background:var(--teal);color:#fff;font-family:'Roboto Condensed',sans-serif;font-weight:700;font-size:8px;display:flex;align-items:center;justify-content:center;gap:4px}
.card .btn{position:absolute;left:10px;top:118px;width:74px;height:19px}

/* search */
.search{left:466px;top:444px;width:179px;height:217px;background:var(--panel);border:1px solid #e2e2e2}
.search-head{height:32px;background:linear-gradient(180deg,#1cc1aa,#0fa28e);color:#fff;font-family:'Roboto Condensed',sans-serif;font-size:11px;display:flex;align-items:center;justify-content:center}
.lbl{font-size:6.6px;color:#444}
.field{background:#fff;border:1px solid #ccc;height:15px}
.select::after{content:"";position:absolute;right:1px;top:1px;width:9px;height:11px;background:#e6e6e6}
.select{position:absolute}

/* hot */
.hot{left:0;top:678px;width:726px;height:156px;background:var(--panel);border-top:1px solid #e4e4e4;border-bottom:1px solid #e4e4e4}
.prop{width:152px}
.prop .photo{height:86px;border:2px solid #fff;outline:1px solid #ddd}
.prop .name{font-size:8.4px;color:var(--teal);margin-top:8px}
.prop .name span{color:#444}
.prop .meta{font-size:8.2px;color:#555;margin-top:2px}

/* customers */
.speak{left:466px;top:844px;width:178px;height:125px;background:var(--panel);border:1px solid #e2e2e2}
.quote{font-size:7.8px;color:#444;line-height:1.5}
.author{font-size:7px;color:var(--teal);margin-top:4px}

/* footer */
.footer{left:0;top:990px;width:726px;height:176px;background:var(--footer)}
.fcol{top:1008px;font-family:'Roboto Condensed',sans-serif}
.fcol h4{font-weight:400;font-size:8.6px;color:var(--footer-text);padding-bottom:5px;border-bottom:1px dotted var(--footer-line);margin-bottom:0}
.fcol ul{list-style:none}
.fcol li{font-size:7.2px;color:var(--footer-text);height:17.8px;display:flex;align-items:center;gap:16px;border-bottom:1px dotted var(--footer-line);padding-left:3px}
.fcol li:first-child{color:#fff}
.fcol li::before{content:"";width:5px;height:5px;border:1px solid #3fae7e;background:#1e7a56}
.social{display:flex;gap:5px;margin-top:10px}
.social i{width:15px;height:15px;background:#4c8cb6;display:block}
.bottom{left:0;top:1166px;width:726px;height:34px;background:var(--bottom);color:#4f7c6e;font-size:6.5px;display:flex;align-items:center;justify-content:center}
</style>
</head>
<body>

<!-- header -->
<div class="abs brand"><div class="name">Lantern Dwelling</div><div class="sub">PARTNERS</div></div>
<div class="abs contact" style="left:450px">
  <svg viewBox="0 0 10 10"><circle cx="5" cy="5" r="4.3" fill="none" stroke="#6cb52d"/><path d="M3.3 3c.3 1.8 1.6 3.3 3.4 3.8l.5-.8-1-.6-.5.4c-.7-.4-1.2-1-1.5-1.7l.4-.5-.6-1z" fill="#6cb52d"/></svg>
  01 5550 2214 / 15</div>
<div class="abs contact" style="left:542px">
  <svg viewBox="0 0 10 10"><circle cx="5" cy="5" r="4.3" fill="none" stroke="#6cb52d"/><circle cx="5" cy="5" r="1.6" fill="none" stroke="#6cb52d"/></svg>
  info@lanterndwelling.com</div>
<nav class="abs nav">
  <a class="active">HOME</a><a>ABOUT US</a><a>BUYING</a><a>SELLING</a><a>INVESTORS</a><a>SERVICES</a><a>CONTACTS</a>
</nav>

<!-- hero -->
<div class="abs hero" role="img" aria-label="City skyline of glass towers over a green park, with a smiling agent in a suit, arms crossed"></div>
<div class="abs hero-title">WARM ENVIRONMENTS</div>
<div class="abs hero-text">Lorem Ipsum is simply dummy text of the printing and typesetting  simply dummy industry.</div>
<div class="abs dots"><i></i><i></i><i></i></div>

<!-- news -->
<div class="abs news">
  <div class="abs news-title">News &amp; Updates</div>
  <div class="abs news-sep"></div>
  <div class="abs news-text">Lorem Ipsum is simply dummy text of the printing and typesetting industry Ipsum is simply inting and type set.</div>
</div>

<!-- ongoing project -->
<div class="abs h2" style="left:83px;top:455px">Ongoing Project
  <svg width="10" height="9" viewBox="0 0 10 9" style="vertical-align:-1px;margin-left:2px"><rect x="0.5" y="0.5" width="9" height="8" fill="none" stroke="#6cb52d"/><rect x="2" y="2.5" width="3" height="3" fill="#6cb52d"/><path d="M6 3h2.5M6 5h2.5" stroke="#6cb52d"/></svg></div>
<div class="abs rule" style="left:83px;top:477px;width:365px"></div>
<p class="abs copy" style="left:84px;top:482px;width:350px">Lorem Ipsum is simply dummy text of the printing and typesetting industry. Lorem Ipsum is simply dummy text of the printing and typesetting industry.</p>

<div class="abs card" style="left:83px;top:516px">
  <div class="title">Project Title, <span>LA</span></div>
  <div class="photo" role="img" aria-label="Residential high-rise towers at sunset" style="background:linear-gradient(180deg,#b9c6d6,#8c9aa8 60%,#4c6a3a)"></div>
  <div class="info">2, 3 &amp; 4 BR Multistorey Apartments<br>Price Starting $ 45000 Onwards</div>
  <div class="btn">Get Details <span>&#9658;</span></div>
</div>
<div class="abs card" style="left:270px;top:516px">
  <div class="title">Project Title, <span>LA</span></div>
  <div class="photo" role="img" aria-label="Apartment blocks around a landscaped courtyard" style="background:linear-gradient(180deg,#c7c9c4,#9a9888 55%,#5a6a45)"></div>
  <div class="info">2, 3 &amp; 4 BR Multistorey Apartments<br>Price Starting $ 35000 Onwards</div>
  <div class="btn">Get Details <span>&#9658;</span></div>
</div>

<!-- search -->
<div class="abs search">
  <div class="search-head">Search Property</div>
  <div class="abs lbl" style="left:14px;top:41px">Price per month (Rs)</div>
  <div class="abs field" style="left:14px;top:52px;width:66px"></div>
  <div class="abs lbl" style="left:87px;top:55px">To</div>
  <div class="abs field" style="left:102px;top:52px;width:66px"></div>
  <div class="abs lbl" style="left:14px;top:74px">Location</div>
  <div class="select field" style="left:14px;top:85px;width:154px"></div>
  <div class="abs lbl" style="left:14px;top:108px">Min bedrooms</div>
  <div class="select field" style="left:14px;top:119px;width:66px"></div>
  <div class="abs lbl" style="left:102px;top:108px">Property type</div>
  <div class="select field" style="left:102px;top:119px;width:66px"></div>
  <div class="abs lbl" style="left:14px;top:141px">Availability</div>
  <div class="select field" style="left:14px;top:152px;width:66px"></div>
  <div class="abs lbl" style="left:102px;top:142px">Furnished</div>
  <div class="select field" style="left:102px;top:152px;width:66px"></div>
  <div class="abs lbl" style="left:14px;top:175px">Enter your E-mail Id</div>
  <div class="abs field" style="left:14px;top:186px;width:120px;height:18px"></div>
  <div class="abs btn" style="left:140px;top:186px;width:28px;height:17px">Go</div>
</div>

<!-- hot properties -->
<div class="abs hot"></div>
<div class="abs h2" style="left:83px;top:685px">Hot Properties</div>
<svg class="abs" style="left:84px;top:751px" width="8" height="18" viewBox="0 0 8 18"><path d="M7 1 1 9l6 8" fill="none" stroke="#999" stroke-width="1.3"/></svg>
<svg class="abs" style="left:636px;top:751px" width="8" height="18" viewBox="0 0 8 18"><path d="M1 1l6 8-6 8" fill="none" stroke="#999" stroke-width="1.3"/></svg>
<div class="abs prop" style="left:122px;top:706px">
  <div class="photo" role="img" aria-label="Modern apartment building with trees" style="background:linear-gradient(180deg,#e6ecef,#9fa9a6 55%,#4f6b3c)"></div>
  <div class="name">Maple Crest Valley, <span>LA</span></div>
  <div class="meta">1 min from ongoing E.M. Bypass</div>
</div>
<div class="abs prop" style="left:287px;top:706px">
  <div class="photo" role="img" aria-label="Glass office block with palm trees" style="background:linear-gradient(180deg,#6d97c6,#9cb3c8 50%,#7f8f88)"></div>
  <div class="name">Harbor Glass Tower, <span>LA</span></div>
  <div class="meta">1 min from ongoing E.M. Bypass</div>
</div>
<div class="abs prop" style="left:452px;top:706px">
  <div class="photo" role="img" aria-label="Contemporary family home with wood facade" style="background:linear-gradient(135deg,#3f6e2e,#a0774f 50%,#d8d2c6)"></div>
  <div class="name">Willow Park - Lake Home, <span>LA</span></div>
  <div class="meta">1 min from ongoing E.M. Bypass</div>
</div>

<!-- welcome -->
<div class="abs h2" style="left:84px;top:847px">Welcome to our site
  <svg width="10" height="10" viewBox="0 0 10 10" style="vertical-align:-1px;margin-left:2px"><path d="M2 6a3 3 0 0 1 5-3M8 4a3 3 0 0 1-5 3" fill="none" stroke="#6cb52d" stroke-width="1.3"/></svg></div>
<div class="abs rule" style="left:84px;top:866px;width:364px"></div>
<div class="abs" role="img" aria-label="Smiling businesswoman holding a small model house" style="left:84px;top:872px;width:122px;height:118px;background:linear-gradient(180deg,#f1efec,#c9c4bd 45%,#2b2b2e)"></div>
<p class="abs copy" style="left:214px;top:869px;width:232px;font-size:7.9px">Lorem Ipsum is simply dummy text of the printing and typesetting industry. Lorem Ipsum has been the industry's standard dummy text ever since the 1500s, when an unknown printer took a galley of type and scrambled it to centuries, but also the leap into electronic typesetting, remaining essentially unchanged.</p>
<div class="abs btn" style="left:215px;top:950px;width:74px;height:18px">Know More <span>&#9658;</span></div>

<!-- customers -->
<div class="abs speak">
  <div class="abs h2" style="left:13px;top:9px">Customers Speak
    <svg width="9" height="8" viewBox="0 0 9 8" style="margin-left:2px"><path d="M0 0h9v5H4L2 8V5H0z" fill="#6cb52d"/></svg></div>
  <div class="abs rule" style="left:13px;top:26px;width:152px"></div>
  <div class="abs" style="left:14px;top:30px;width:155px">
    <p class="quote">Lorem Ipsum is simply dummy text of the printing and typesetting industry.</p>
    <p class="author">R.M. Calloway</p>
    <p class="quote" style="margin-top:9px">Lorem Ipsum is simply dummy text of the printing and typesetting industry.</p>
    <p class="author">R.M. Calloway</p>
  </div>
</div>

<!-- footer -->
<div class="abs footer"></div>
<div class="abs fcol" style="left:85px;width:167px">
  <h4>Company Profile</h4>
  <ul><li>Go to Home</li><li>Go to About Us</li><li>Go to Buying</li><li>Go to Selling</li><li>Go to Investors</li><li>Go to Services</li><li>Go to Contacts</li></ul>
</div>
<div class="abs fcol" style="left:286px;width:160px">
  <h4>Our Services</h4>
  <ul><li style="color:var(--footer-text)">Residential</li><li>Hi-end Residential</li><li>Commercial</li><li>Investment</li><li>Industrial Land &amp; Ware Housing</li><li>Search Agents</li><li>Register Now</li></ul>
</div>
<div class="abs fcol" style="left:478px;width:166px">
  <h4>Subscribe Us</h4>
  <p style="font-size:7.2px;color:var(--footer-text);margin-top:6px">Subscribe to our Market Reports &amp; Real-Ties.</p>
  <div style="margin-top:6px;height:16px;background:#2f7a62;border:1px solid #4d977d;font-size:6.5px;color:#cfe6dd;padding:4px 6px">Your Email id</div>
  <div class="btn" style="margin-top:5px;width:64px;height:16px;font-weight:400;font-size:7.2px">Subscribe Now</div>
  <h4 style="margin-top:10px">Follow Us</h4>
  <div class="social"><i></i><i></i><i></i><i></i></div>
</div>
<div class="abs bottom">Copyright@2016. All rights are reserved.</div>

</body>
</html>
```